Brenwick Coaching Website

I would like someone to design my website. I have an existing site which is really basic and needs an overhaul. I have attached a powerpoint with all the information I require. I am flexible with the design and layout and am ok with graphics being added to enhance the attractiveness of the site.

```html
<!DOCTYPE html>
<html lang="en">
<head>
<meta charset="utf-8">
<title>Brenwick Coaching</title>
<link rel="stylesheet" href="https://fonts.googleapis.com/css2?family=Open+Sans:wght@300;400;600;700&display=swap">
<style>
  :root {
    --band: #f7f7f7;
    --page: #ffffff;
    --panel: #f4f4f4;
    --ink: #222222;
    --muted: #555555;
    --brand-blue: #1c6db4;
    --orange-top: #f7946a;
    --orange-bottom: #e6431a;
    --orange-edge: #8c2a0c;
    --cta-top: #2c98d6;
    --cta-bottom: #0a539e;
    --white: #ffffff;
    --mail: #ee5a2a;
  }
  * { box-sizing: border-box; margin: 0; padding: 0; }
  html, body { width: 1200px; height: 707px; overflow: hidden; }
  body {
    position: relative;
    background: var(--page);
    font-family: "Open Sans", Arial, sans-serif;
    color: var(--ink);
  }
  .site-header {
    position: absolute; left: 0; top: 0; width: 1200px; height: 109px;
    background: var(--band);
  }
  .brand {
    position: absolute; left: 49px; top: 38px;
    display: flex; align-items: center; gap: 10px;
  }
  .brand-mark { width: 22px; height: 22px; background: var(--mail); }
  .brand-name {
    font-size: 27px; font-weight: 400; color: var(--brand-blue); line-height: 1;
  }
  .contact {
    position: absolute; right: 57px; top: 33px; text-align: right;
  }
  .contact-phone {
    display: flex; align-items: center; justify-content: flex-end; gap: 8px;
    font-size: 31px; font-weight: 300; color: #444; line-height: 1;
  }
  .contact-mail {
    display: flex; align-items: center; justify-content: flex-end; gap: 10px;
    margin-top: 13px; font-size: 15px; color: #444;
  }
  .nav-button {
    position: absolute; left: 42px; width: 351px; height: 106px;
    border-radius: 7px;
    background: linear-gradient(to bottom, var(--orange-top) 0%, #f06a3a 45%, var(--orange-bottom) 100%);
    border-bottom: 5px solid var(--orange-edge);
    color: var(--white); font-weight: 700; font-size: 21px;
    display: flex; align-items: center; justify-content: space-between;
    padding: 0 24px 0 30px; text-decoration: none;
    text-shadow: 0 1px 1px rgba(0,0,0,.25);
  }
  .welcome {
    position: absolute; left: 417px; top: 135px; width: 726px; height: 323px;
    background: var(--panel); border-radius: 9px;
  }
  .welcome-copy {
    position: absolute; left: 24px; top: 70px; width: 478px;
  }
  .welcome-title {
    font-size: 35px; font-weight: 300; color: var(--brand-blue);
    letter-spacing: -0.8px; line-height: 44px; white-space: nowrap;
  }
  .welcome-text {
    margin-top: 20px;
    font-size: 14.5px; line-height: 33px; color: var(--ink); letter-spacing: -0.3px;
  }
  .portrait {
    position: absolute; left: 509px; top: 62px; width: 201px; height: 208px;
    border-radius: 8px;
    background: linear-gradient(160deg, #b7ad9e 0%, #8a7a66 45%, #3a2a22 100%);
  }
  .portrait-caption {
    position: absolute; left: 509px; top: 287px; width: 201px; text-align: center;
    font-size: 16px; font-weight: 600; color: #333;
  }
  .cta {
    position: absolute; left: 417px; top: 485px; width: 726px; height: 101px;
    border-radius: 8px;
    background: linear-gradient(to bottom, var(--cta-top) 0%, #1f82c6 46%, #0e5fab 47%, var(--cta-bottom) 100%);
    color: var(--white); font-weight: 700; font-size: 19px; letter-spacing: 0.6px;
    display: flex; align-items: center; justify-content: center;
    text-decoration: none;
  }
  .site-footer {
    position: absolute; left: 0; top: 619px; width: 1200px; height: 88px;
    background: var(--band);
  }
  .copyright {
    position: absolute; left: 0; width: 1200px; top: 32px; text-align: center;
    font-size: 16px; color: var(--muted);
  }
  .social {
    position: absolute; right: 58px; top: 30px; display: flex; gap: 14px;
  }
  .social-dot { width: 26px; height: 26px; border-radius: 50%; background: #111; }
</style>
</head>
<body>
  <header class="site-header">
    <div class="brand">
      <span class="brand-mark"></span>
      <span class="brand-name">Brenwick Coaching</span>
    </div>
    <div class="contact">
      <div class="contact-phone">
        <svg width="22" height="26" viewBox="0 0 22 26" aria-hidden="true">
          <path d="M5 2 L9 1 L11 8 L8 10 C9 14 11 17 14 19 L17 16 L22 21 L19 25 C10 23 3 14 2 5 Z" fill="#1c6db4"/>
        </svg>
        <span>1300 555 018</span>
      </div>
      <div class="contact-mail">
        <svg width="24" height="17" viewBox="0 0 24 17" aria-hidden="true">
          <rect x="1" y="1" width="22" height="15" fill="none" stroke="#ee5a2a" stroke-width="2"/>
          <path d="M1 1 L12 10 L23 1" fill="none" stroke="#ee5a2a" stroke-width="2"/>
        </svg>
        <span>mara.hollis@brenwickcoaching.com</span>
      </div>
    </div>
  </header>

  <nav class="main-nav">
    <a class="nav-button" style="top:135px" href="#">Individual Coaching
      <svg width="20" height="32" viewBox="0 0 20 32" aria-hidden="true"><path d="M3 3 L16 16 L3 29" fill="none" stroke="#fff" stroke-width="5"/></svg></a>
    <a class="nav-button" style="top:247px" href="#">Group Work
      <svg width="20" height="32" viewBox="0 0 20 32" aria-hidden="true"><path d="M3 3 L16 16 L3 29" fill="none" stroke="#fff" stroke-width="5"/></svg></a>
    <a class="nav-button" style="top:361px" href="#">Resources
      <svg width="20" height="32" viewBox="0 0 20 32" aria-hidden="true"><path d="M3 3 L16 16 L3 29" fill="none" stroke="#fff" stroke-width="5"/></svg></a>
    <a class="nav-button" style="top:478px" href="#">Inspiration Booth
      <svg width="20" height="32" viewBox="0 0 20 32" aria-hidden="true"><path d="M3 3 L16 16 L3 29" fill="none" stroke="#fff" stroke-width="5"/></svg></a>
  </nav>

  <section class="welcome">
    <div class="welcome-copy">
      <h1 class="welcome-title">Welcome to Brenwick Coaching</h1>
      <p class="welcome-text">Where we put a new perspective on the way you work, live and play. Through our programs you will learn new skills &amp; techniques to enable you to break through the barriers that have kept you from reaching your full potential up to now.</p>
    </div>
    <div class="portrait" role="img" aria-label="Portrait photograph of coach Mara outdoors among trees"></div>
    <p class="portrait-caption">About Mara</p>
  </section>

  <a class="cta" href="#">GET YOUR FREE 30 MINUTE INTRODUCTORY COACHING SESSION...</a>

  <footer class="site-footer">
    <p class="copyright">© 2014 Company Name ,All Rights Reserved</p>
    <div class="social">
      <span class="social-dot" aria-label="Social link"></span>
      <span class="social-dot" aria-label="Social link"></span>
      <span class="social-dot" aria-label="Social link"></span>
    </div>
  </footer>
</body>
</html>
```